Business Card: RW Office Partners - Your organised problem solver

Business Name: RW Office Partners
Website: www.rwofficepartners.com.au
Email: marisol@rwofficepartners.com.au
Mobile: 61 482 907 236
Facebook: @rwofficepartners
Instrgram: @rwofficepartners

Brading Colours:
HEX
#986474
#ddccd3
#7a8498
#c9d8e4
#000000
#ffffff

Tag Line: Your organised problem solver

Link to DRAFT website:
https://deskhelpcollective.wixsite.com/rw-office-partners

About Page from the website:
My name is Marisol Wrenfield, and I would love to assist you to become more productive in your day to day and achieve your business and personal goals.
My mission is to give you time, time to work on the important tasks of your business or to be able to spend more time with your family. I will take on the tasks you don’t have time for, don’t know well or simply don’t like to do.
I have an extensive background in Administration, Tender Coordination, Document Control, WHS and Quality Management working primarily in the Construction, Mining and Corporate World.
I am passionate about being organised, having order and making things in your life (and mine) easier! I love to watch something unfold and grow into something amazing! I am known for being the go-to problem solver, the organiser of all things, producing high standards of work even under pressure. I’m also a confident communicator, and I understand that you’re busy running your business.

Target Market(s)

Small to Medium Business who require assistance in their business by a virtual assistant.

Industry/Entity Type

Virtual Assistant

Contact Information for Business Card

Mobile: 61 482 907 236

Font styles to use
Sans Serif

Colors
ffffff

Requirements
Must have
• Branding Colours as outlined.
Contact Details as outlined.
Logo as provided.
Proper contact details - mobile, facebook, instragm, website.
Simple, Elegant, very clean looking.
Should not have
• Note cute with pictures.
Not too girly as still want to market to construction companies.

```html
<!DOCTYPE html>
<html lang="en">
<head>
<meta charset="utf-8">
<title>RW Office Partners – Business Card</title>
<link rel="stylesheet" href="https://fonts.googleapis.com/css2?family=Archivo:wght@600;800&family=Open+Sans:wght@400&display=swap">
<style>
  :root {
    --mauve: #986474;
    --mauve-light: #ddccd3;
    --slate: #7a8498;
    --mist: #c9d8e4;
    --white: #ffffff;
    --pattern-base: #f1f5f9;
  }
  * { margin: 0; padding: 0; box-sizing: border-box; }
  html, body {
    width: 1200px;
    height: 750px;
    overflow: hidden;
    background: var(--white);
  }
  .card {
    position: relative;
    width: 1200px;
    height: 750px;
    overflow: hidden;
    background: var(--white);
  }
  .monogram-field {
    position: absolute;
    inset: 0 0 auto 0;
    height: 560px;
    background: linear-gradient(180deg, var(--pattern-base) 0%, #e9f0f5 100%);
  }
  .base-curves {
    position: absolute;
    left: 0;
    top: 0;
    width: 1200px;
    height: 750px;
  }
  .brand {
    position: absolute;
    left: 0;
    right: 0;
    top: 236px;
    display: flex;
    flex-direction: column;
    align-items: center;
  }
  .brand-lockup {
    display: flex;
    align-items: center;
    gap: 26px;
  }
  .brand-mark {
    width: 96px;
    height: 96px;
    background: var(--mauve);
  }
  .brand-name {
    font-family: "Archivo", sans-serif;
    font-weight: 600;
    font-size: 50px;
    line-height: 50px;
    letter-spacing: 2px;
    color: var(--slate);
    text-transform: uppercase;
  }
  .tagline {
    margin-top: 18px;
    font-family: "Archivo", sans-serif;
    font-weight: 800;
    font-size: 25px;
    letter-spacing: 0.5px;
    color: var(--slate);
    text-transform: uppercase;
  }
  .website {
    position: absolute;
    left: 0;
    right: 0;
    top: 598px;
    text-align: center;
    font-family: "Open Sans", sans-serif;
    font-weight: 400;
    font-size: 30px;
    color: var(--mauve-light);
  }
</style>
</head>
<body>
  <main class="card">
    <div class="monogram-field" role="img" aria-label="Faint repeating monogram pattern background"></div>

    <svg class="base-curves" viewBox="0 0 1200 750" aria-hidden="true">
      <path d="M0 440 Q 330 520 600 530 Q 870 520 1200 440 L1200 750 L0 750 Z" fill="var(--slate)"/>
      <path d="M0 482 Q 300 545 600 542 Q 900 540 1200 482 L1200 750 L0 750 Z" fill="var(--mauve)"/>
    </svg>

    <section class="brand">
      <div class="brand-lockup">
        <div class="brand-mark"></div>
        <h1 class="brand-name">RW Office<br>Partners</h1>
      </div>
      <p class="tagline">Your organised problem solver</p>
    </section>

    <p class="website">www.rwofficepartners.com.au</p>
  </main>
</body>
</html>
```